New website for concierge mobile medical service

new website for business:
WEBSITE REQUEST LIST:
Luxury product look.
Professional. Clean & simple, NO stock people photos. Graphics OK.
Black and white text.

```html
<!DOCTYPE html>
<html lang="en">
<head>
<meta charset="utf-8">
<title>Lumen Care — Contact Us</title>
<link href="https://fonts.googleapis.com/css2?family=Lato:wght@400;700;900&display=swap" rel="stylesheet">
<style>
:root{
  --ink:#2a2a2a;
  --navy:#1d3d4a;
  --violet:#7b6fb5;
  --field-border:#e3e3e3;
  --submit:#9dd6de;
  --footer:#2a2a2a;
  --white:#ffffff;
}
*{margin:0;padding:0;box-sizing:border-box}
html,body{width:1200px;height:954px;overflow:hidden;background:var(--white);font-family:'Lato',sans-serif;color:var(--ink)}
.page{position:relative;width:1200px;height:954px}

.site-header{position:absolute;left:0;top:0;width:1200px;height:107px;background:var(--white)}
.brand{position:absolute;left:156px;top:18px;width:124px;height:124px;border-radius:50%;background:var(--white);z-index:3;display:flex;align-items:center;justify-content:center}
.brand-name{font-weight:700;font-size:19px;color:var(--navy);line-height:1.1;text-align:center}
.phone{position:absolute;left:887px;top:16px;display:flex;align-items:center;gap:12px}
.phone-icon{width:32px;height:32px;background:var(--violet);border-radius:2px;display:flex;align-items:center;justify-content:center}
.phone-number{font-weight:700;font-size:19px;color:var(--violet)}
.main-nav{position:absolute;top:75px;left:0;width:1200px;height:32px}
.main-nav a{position:absolute;top:0;font-weight:700;font-size:13px;color:var(--ink);text-decoration:none;letter-spacing:.2px}
.main-nav a.active{color:var(--navy)}
.nav-underline{position:absolute;left:972px;top:101px;width:93px;height:6px;background:var(--navy)}

.hero{position:absolute;left:0;top:107px;width:1200px;height:265px;background:linear-gradient(90deg,#010b12 0%,#02233a 45%,#04476e 100%)}
.hero-title{position:absolute;left:142px;top:104px;font-weight:700;font-size:45px;color:var(--white);line-height:1}
.hero-graphic{position:absolute;left:866px;top:30px;width:204px;height:204px;border-radius:50%;border:4px solid #8fd4ea;background:radial-gradient(circle,#0b4b73 0%,#06365a 100%)}

.contact{position:absolute;left:0;top:372px;width:1200px;height:447px}
.contact-title{position:absolute;top:40px;width:1200px;text-align:center;font-weight:700;font-size:32px;color:var(--ink)}
.contact-intro{position:absolute;top:93px;width:1200px;text-align:center;font-size:15px;letter-spacing:.2px}
.field{position:absolute;height:40px;border:2px solid var(--field-border);background:var(--white);font-size:12.5px;color:var(--ink);padding:11px 14px}
.field.message{height:100px;padding-top:17px}
.submit{position:absolute;left:277px;top:350px;width:648px;height:44px;background:var(--submit);color:var(--white);font-weight:700;font-size:16px;display:flex;align-items:center;justify-content:center;border-radius:2px}

.site-footer{position:absolute;left:0;top:819px;width:1200px;height:135px;background:var(--footer);color:var(--white)}
.footer-nav a{position:absolute;top:23px;font-weight:700;font-size:13px;color:var(--white);text-decoration:none}
.copyright{position:absolute;top:59px;width:1200px;text-align:center;font-size:11px}
.social{position:absolute;top:89px;left:523px;display:flex;gap:18px}
.social span{width:16px;height:16px;border-radius:50%;background:var(--white)}
</style>
</head>
<body>
<div class="page">
  <header class="site-header">
    <div class="brand"><span class="brand-name">Lumen<br>Care</span></div>
    <div class="phone">
      <span class="phone-icon">
        <svg width="16" height="16" viewBox="0 0 24 24"><path fill="#fff" d="M6.6 10.8a15 15 0 0 0 6.6 6.6l2.2-2.2c.3-.3.7-.4 1-.2 1.1.4 2.3.6 3.6.6.6 0 1 .4 1 1V20c0 .6-.4 1-1 1A17 17 0 0 1 3 4c0-.6.4-1 1-1h3.5c.6 0 1 .4 1 1 0 1.3.2 2.5.6 3.6.1.3 0 .7-.2 1z"/></svg>
      </span>
      <span class="phone-number">555-010-0199</span>
    </div>
    <nav class="main-nav">
      <a style="left:394px">HOME</a>
      <a style="left:474px">ABOUT US</a>
      <a style="left:579px">WHY LUMEN?</a>
      <a style="left:695px">SERVICE AREA</a>
      <a style="left:826px">OTHER</a>
      <a style="left:910px">FAQ</a>
      <a class="active" style="left:974px">CONTACT US</a>
    </nav>
  </header>
  <div class="nav-underline"></div>

  <section class="hero" role="img" aria-label="Dark blue network pattern banner">
    <h1 class="hero-title">Contact Us</h1>
    <div class="hero-graphic" role="img" aria-label="Icon of a medical car with a caduceus"></div>
  </section>

  <section class="contact">
    <h2 class="contact-title">Contact Us</h2>
    <p class="contact-intro">We want to hear from you! Click below to send us a message and receive upcoming information.</p>
    <div class="field" style="left:224px;top:130px;width:365px">Enter Name</div>
    <div class="field" style="left:613px;top:130px;width:366px">Enter Email Address</div>
    <div class="field" style="left:224px;top:182px;width:365px">Phone No</div>
    <div class="field" style="left:613px;top:182px;width:366px">Subject</div>
    <div class="field message" style="left:224px;top:234px;width:755px">Message</div>
    <div class="submit">SUBMIT NOW</div>
  </section>

  <footer class="site-footer">
    <nav class="footer-nav">
      <a style="left:302px">HOME</a>
      <a style="left:381px">ABOUT US</a>
      <a style="left:486px">WHY LUMEN?</a>
      <a style="left:602px">SERVICE AREA</a>
      <a style="left:733px">OTHER</a>
      <a style="left:816px">CONTACT US</a>
    </nav>
    <p class="copyright">Copyright &copy; 2019.&nbsp; Company Name&nbsp; All Rights Reserved</p>
    <div class="social"><span></span><span></span><span></span><span></span><span></span></div>
  </footer>
</div>
</body>
</html>
```